Salon and Spa Distributor Business Card

Need a business card. We are are distributor in the salon and spa industry. We identify with natural beauty. Need a card with:
Company Name: Petal Quarry"
Title: "President & CEO"
Address
Company Phone number
email
website
Tag Line:" Pure Supply for Every Salon"

Industry/Entity Type

Business

Contact Information for Business Card

Name: Dov Strommen
Title: "President & CEO"
Address: 31 Harlow Ln, Bexmoor, NJ 07813
Company Phone number: 800-463-5918
email: dovstrommen@petalquarry.example
website: www.petalquarry.example

Requirements
Should not have
• No black backgrounds

```html
<!DOCTYPE html>
<html lang="en">
<head>
<meta charset="utf-8">
<title>Petal Quarry – Business Card</title>
<link href="https://fonts.googleapis.com/css2?family=Didact+Gothic&display=swap" rel="stylesheet">
<style>
  :root {
    --page-bg: #ececec;
    --leaf-light: #62b946;
    --leaf-mid: #2f9a3f;
    --leaf-dark: #0f6b35;
    --brand-green: #3aa43f;
    --ink: #1c1c1c;
    --paper: #ffffff;
  }
  * { box-sizing: border-box; margin: 0; padding: 0; }
  html, body {
    width: 1200px;
    height: 880px;
    overflow: hidden;
    background: var(--page-bg);
    font-family: "Didact Gothic", "Century Gothic", sans-serif;
  }
  .canvas { position: relative; width: 1200px; height: 880px; }
  .card {
    position: absolute;
    width: 620px;
    height: 354px;
    border-radius: 22px;
    overflow: hidden;
    box-shadow: 0 10px 26px rgba(0,0,0,0.18);
  }

  /* Front */
  .card-front {
    left: 60px;
    top: 60px;
    background: linear-gradient(160deg, var(--leaf-light) 0%, var(--leaf-mid) 50%, var(--leaf-dark) 100%);
    color: var(--paper);
  }
  .front-lockup {
    position: absolute;
    left: 0;
    right: 0;
    top: 120px;
    display: flex;
    align-items: center;
    justify-content: center;
    gap: 18px;
  }
  .brand-dot {
    width: 22px;
    height: 22px;
    border-radius: 50%;
    background: var(--paper);
  }
  .front-name { font-size: 50px; letter-spacing: 1px; line-height: 1; white-space: nowrap; }
  .front-tagline {
    position: absolute;
    left: 0;
    right: 0;
    top: 216px;
    text-align: center;
    font-size: 16px;
    letter-spacing: 4px;
    white-space: nowrap;
  }

  /* Back */
  .card-back {
    left: 520px;
    top: 466px;
    background: var(--paper);
    color: var(--ink);
  }
  .back-art {
    position: absolute;
    left: 0;
    bottom: 0;
    width: 300px;
    height: 354px;
    background: radial-gradient(ellipse at 35% 70%, var(--leaf-light) 0%, var(--leaf-mid) 45%, rgba(255,255,255,0) 75%);
  }
  .back-info {
    position: absolute;
    right: 40px;
    top: 36px;
    text-align: right;
    white-space: nowrap;
  }
  .back-name { color: var(--brand-green); font-size: 38px; line-height: 1; }
  .back-tagline { font-size: 13px; margin-top: 4px; }
  .person { margin-top: 34px; }
  .person-name { color: var(--brand-green); font-size: 20px; }
  .person-title { font-size: 14px; }
  .contact { margin-top: 26px; font-size: 14px; line-height: 1.55; list-style: none; }
  .contact .domain { color: var(--brand-green); }
</style>
</head>
<body>
<main class="canvas">
  <section class="card card-front" aria-label="Card front">
    <div class="front-lockup">
      <span class="brand-dot"></span>
      <span class="front-name">Petal Quarry</span>
    </div>
    <p class="front-tagline">Pure Supply for Every Salon</p>
  </section>

  <section class="card card-back" aria-label="Card back">
    <div class="back-art" role="img" aria-label="Large green illustration of a profile with flowing hair and leaves"></div>
    <div class="back-info">
      <h1 class="back-name">Petal Quarry</h1>
      <p class="back-tagline">Pure Supply for Every Salon</p>
      <div class="person">
        <p class="person-name">Dov Strommen</p>
        <p class="person-title">President &amp; CEO</p>
      </div>
      <ul class="contact">
        <li>800-463-5918</li>
        <li>dovstrommen@petalquarry.example</li>
        <li>www.<span class="domain">petalquarry</span>.example</li>
        <li>31 Harlow Ln, Bexmoor, NJ 07813</li>
      </ul>
    </div>
  </section>
</main>
</body>
</html>
```